Briefpapier und Visitenkarten für Bayerisches Gasthaus mit Zimmer
Zielgruppe
Traditionelle Gaststätte im Zentrum einer Kleinstadt in Bayern. Direkt am Marktplatz. 10 Gästezimmer.
Bayerisch. Traditionell. Von junger Geschäftsführerin geführt, mit jungem Personal. Wir haben das Objekt erst vor Kurzem erworben und fangen gerade an.
Gerichte: Braten, Steaks, Brotzeiten, vegetarische und VEGANE Speisen
Getränke: Sehr bierlastig. Es war früher ein Brauereigasthaus. Heute gibts auch eine kleine feine Weinkarte.
Zielgruppe sind Einheimische und Touristen. Im Sommer kommen Radfahrer und Wanderer. Besonders angesprochen werden auch Kinder. Es gibt eine großzügige Spielecke.
Aufgabenstellung
Das Gasthaus heißt Falke. Daher spielt der Falke im Design auch eine wichtige Rolle.
Nachdem wir sehr familienorientiert sind, könnte ich mir auch eine Falke-Familie vorstellen.
Visitenkarten und Briefpapier sollen alle wichtigen Infos enthalten, aber dabei sehr klar gehalten werden und nicht überladen sein. Mir ist ein schlichtes und ansprechendes Design wichtig. Es soll nicht verspielt sein.
Hier ist die Homepage:
www.falke-haldenau-gast.de
Info auf Briefpapier:
GASTHAUS FALKE
Trauber GmbH
Als Info auf Visitenkarte:
Gasthaus Falke

```html
<!DOCTYPE html>
<html lang="de">
<head>
<meta charset="utf-8">
<title>Gasthaus Falke – Visitenkarten</title>
<link href="https://fonts.googleapis.com/css2?family=Cinzel:wght@400&family=Source+Sans+3:wght@400;600;700&display=swap" rel="stylesheet">
<style>
  :root {
    --stage: #76767a;
    --green: #a8c520;
    --green-pale: #cfe08a;
    --green-faint: #f4f7e8;
    --charcoal: #545454;
    --ink: #555555;
    --ink-soft: #7a7a7a;
    --grey-title: #9a9a9a;
    --grey-serif: #bdbdbd;
    --white: #ffffff;
  }
  * { margin: 0; padding: 0; box-sizing: border-box; }
  html, body { width: 1200px; height: 1008px; overflow: hidden; }
  body { background: var(--stage); position: relative; font-family: "Source Sans 3", sans-serif; }

  .card { position: absolute; width: 408px; height: 258px; overflow: hidden; }
  .card--green { left: 120px; top: 172px; background: var(--green); color: var(--white); }
  .card--bars { left: 672px; top: 172px; background: var(--white); color: var(--ink); border-top: 9px solid var(--green); border-bottom: 10px solid var(--green); }
  .card--dark { left: 120px; top: 576px; background: var(--charcoal); }
  .card--light { left: 672px; top: 576px; background: var(--white); color: var(--ink-soft); }

  .illustration { position: absolute; }
  .wordmark { position: absolute; font-weight: 400; line-height: 0.92; font-size: 32px; letter-spacing: 0.5px; }
  .wordmark--sans { font-family: "Source Sans 3", sans-serif; }
  .wordmark--serif { font-family: "Cinzel", serif; letter-spacing: 2px; left: 0; right: 0; text-align: center; line-height: 1; }
  .locality { position: absolute; font-size: 12.5px; font-weight: 700; text-align: right; line-height: 15px; letter-spacing: 0.4px; }

  .contact { position: absolute; left: 0; top: 0; list-style: none; font-size: 13px; line-height: 16px; }
  .contact li { position: absolute; padding-left: 18px; white-space: nowrap; }
  .contact .icon { position: absolute; left: 0; top: 1px; width: 13px; height: 14px; }
  .contact .icon--at { font-weight: 700; top: 0; width: auto; height: auto; }
  .card--green .icon { fill: var(--white); color: var(--white); }
  .card--bars .icon, .card--light .icon { fill: var(--green); color: var(--green); }
  .card--light .contact { letter-spacing: 0.6px; }

  .rule { position: absolute; }
</style>
</head>
<body>

<!-- Card 1: green front -->
<section class="card card--green">
  <div class="illustration" role="img" aria-label="Falkenfamilie auf Wasserlinie, helle Illustration"
       style="left:24px;top:22px;width:190px;height:108px;background:radial-gradient(ellipse at 55% 50%, var(--green-pale) 0%, rgba(207,224,138,0.6) 55%, rgba(207,224,138,0) 72%);"></div>
  <h1 class="wordmark wordmark--sans" style="left:208px;top:20px;">GASTHAUS<br>FALKE</h1>
  <p class="locality" style="right:69px;top:77px;">Haldenau<br>im Lindental</p>
  <div class="rule" style="left:0;right:0;top:174px;height:3px;background:var(--green-pale);"></div>

  <ul class="contact">
    <li style="left:23px;top:186px;"><svg class="icon" viewBox="0 0 12 16"><path d="M6 0a6 6 0 0 0-6 6c0 4.5 6 10 6 10s6-5.5 6-10a6 6 0 0 0-6-6zm0 8.5A2.5 2.5 0 1 1 6 3.5a2.5 2.5 0 0 1 0 5z"/></svg>Trauber GmbH</li>
    <li style="left:23px;top:205px;">Lindenplatz 7</li>
    <li style="left:23px;top:224px;">84321 Haldenau</li>
    <li style="left:203px;top:186px;"><svg class="icon" viewBox="0 0 14 14"><path d="M3 1l2.5 3-1.5 1.5c.8 1.8 2.2 3.2 4 4L9.5 8l3 2.5-1.5 2.5C5.5 12.5 1.5 8.5 1 3z"/></svg>09451 3806</li>
    <li style="left:203px;top:205px;"><span class="icon icon--at">@</span>info@falke-haldenau-gast.de</li>
    <li style="left:203px;top:224px;"><svg class="icon" viewBox="0 0 12 12"><circle cx="6" cy="6" r="5.2" fill="none" stroke="currentColor" stroke-width="1.4"/><path d="M1 6h10M6 1c-2.5 3-2.5 7 0 10M6 1c2.5 3 2.5 7 0 10" fill="none" stroke="currentColor" stroke-width="1"/></svg>www.falke-haldenau-gast.de</li>
  </ul>
</section>

<!-- Card 2: white with green bars -->
<section class="card card--bars">
  <div class="illustration" role="img" aria-label="Falkenfamilie auf Wasserlinie, grüne Illustration"
       style="left:31px;top:14px;width:178px;height:104px;background:radial-gradient(ellipse at 55% 50%, var(--green) 0%, rgba(168,197,32,0.85) 50%, rgba(168,197,32,0) 72%);"></div>
  <h1 class="wordmark wordmark--sans" style="left:214px;top:11px;color:var(--grey-title);">GASTHAUS<br>FALKE</h1>
  <p class="locality" style="right:63px;top:68px;color:var(--grey-title);">Haldenau<br>im Lindental</p>
  <div class="rule" style="left:198px;right:0;top:122px;height:1px;background:var(--green-pale);"></div>

  <ul class="contact">
    <li style="left:199px;top:127px;"><svg class="icon" viewBox="0 0 12 16"><path d="M6 0a6 6 0 0 0-6 6c0 4.5 6 10 6 10s6-5.5 6-10a6 6 0 0 0-6-6zm0 8.5A2.5 2.5 0 1 1 6 3.5a2.5 2.5 0 0 1 0 5z"/></svg>Trauber GmbH</li>
    <li style="left:199px;top:143px;">Lindenplatz 7</li>
    <li style="left:199px;top:159px;">84321 Haldenau</li>
    <li style="left:199px;top:178px;"><svg class="icon" viewBox="0 0 14 14"><path d="M3 1l2.5 3-1.5 1.5c.8 1.8 2.2 3.2 4 4L9.5 8l3 2.5-1.5 2.5C5.5 12.5 1.5 8.5 1 3z"/></svg>09451 3806</li>
    <li style="left:199px;top:198px;"><span class="icon icon--at">@</span>info@falke-haldenau-gast.de</li>
    <li style="left:199px;top:214px;"><svg class="icon" viewBox="0 0 12 12"><circle cx="6" cy="6" r="5.2" fill="none" stroke="currentColor" stroke-width="1.4"/><path d="M1 6h10M6 1c-2.5 3-2.5 7 0 10M6 1c2.5 3 2.5 7 0 10" fill="none" stroke="currentColor" stroke-width="1"/></svg>www.falke-haldenau-gast.de</li>
  </ul>
</section>

<!-- Card 3: dark back -->
<section class="card card--dark">
  <div class="illustration" role="img" aria-label="Zwei Falken auf Wasserlinie, grüne Illustration"
       style="left:124px;top:42px;width:160px;height:110px;background:radial-gradient(ellipse at 50% 55%, var(--green) 0%, rgba(168,197,32,0.85) 48%, rgba(168,197,32,0) 72%);"></div>
  <h1 class="wordmark wordmark--serif" style="top:166px;font-size:28px;color:var(--grey-serif);">GASTHAUS FALKE</h1>
  <p style="position:absolute;left:0;right:0;top:197px;text-align:center;color:var(--white);font-size:12px;font-weight:700;letter-spacing:1.6px;">HALDENAU IM LINDENTAL</p>
  <div class="rule" style="left:126px;width:79px;top:219px;height:2px;background:var(--green);"></div>
  <div class="rule" style="left:211px;width:73px;top:219px;height:2px;background:var(--green);"></div>
</section>

<!-- Card 4: light back -->
<section class="card card--light">
  <div class="illustration" role="img" aria-label="Großer, sehr heller Falke als Hintergrundmotiv"
       style="left:210px;top:0;width:198px;height:258px;background:radial-gradient(ellipse at 60% 55%, var(--green-faint) 0%, var(--green-faint) 55%, rgba(244,247,232,0) 75%);"></div>
  <div class="illustration" role="img" aria-label="Zwei Falken auf Wasserlinie, grüne Illustration"
       style="left:148px;top:25px;width:110px;height:76px;background:radial-gradient(ellipse at 50% 55%, var(--green) 0%, rgba(168,197,32,0.85) 48%, rgba(168,197,32,0) 72%);"></div>
  <h1 class="wordmark wordmark--serif" style="top:110px;font-size:19px;color:var(--ink-soft);">GASTHAUS FALKE</h1>
  <div class="rule" style="left:148px;width:110px;top:134px;height:2px;background:var(--green);"></div>

  <ul class="contact">
    <li style="left:23px;top:183px;"><svg class="icon" viewBox="0 0 12 16"><path d="M6 0a6 6 0 0 0-6 6c0 4.5 6 10 6 10s6-5.5 6-10a6 6 0 0 0-6-6zm0 8.5A2.5 2.5 0 1 1 6 3.5a2.5 2.5 0 0 1 0 5z"/></svg>Trauber GmbH</li>
    <li style="left:23px;top:202px;">Lindenplatz 7</li>
    <li style="left:23px;top:221px;">84321 Haldenau</li>
    <li style="left:186px;top:183px;"><svg class="icon" viewBox="0 0 14 14"><path d="M3 1l2.5 3-1.5 1.5c.8 1.8 2.2 3.2 4 4L9.5 8l3 2.5-1.5 2.5C5.5 12.5 1.5 8.5 1 3z"/></svg>09451 3806</li>
    <li style="left:186px;top:202px;"><span class="icon icon--at">@</span>info@falke-haldenau-gast.de</li>
    <li style="left:186px;top:221px;"><svg class="icon" viewBox="0 0 12 12"><circle cx="6" cy="6" r="5.2" fill="none" stroke="currentColor" stroke-width="1.4"/><path d="M1 6h10M6 1c-2.5 3-2.5 7 0 10M6 1c2.5 3 2.5 7 0 10" fill="none" stroke="currentColor" stroke-width="1"/></svg>www.falke-haldenau-gast.de</li>
  </ul>
</section>

</body>
</html>
```